Meridale Staffing Website

My business has been word of mouth over the last 3 years and has grown. Now I need a website for additional marketing as we have new clients asking for a website.

You have already completed my Logo during an earlier project. I have attached the logo.

We do Staff Augmentation and Operation Support.

What is that?
Staff augmentation is an outsourcing strategy that allows companies to fill specific, temporary roles to achieve business objectives. This staffing method complements existing teams with specific talent, enhancing business capabilities or filling gaps left by members on extended leave.

We work alongside the internal recruiting team to assist clients to meet and exceed financial goals.

```html
<!DOCTYPE html>
<html lang="en">
<head>
<meta charset="utf-8">
<title>Meridale Staffing</title>
<link href="https://fonts.googleapis.com/css2?family=Archivo:wght@800&family=Montserrat:wght@400;500;600;700&display=swap" rel="stylesheet">
<style>
:root{
  --navy:#0b4a72;
  --navy-deep:#0a3f63;
  --ink:#1d1d1d;
  --grey:#6e6e6e;
  --muted:#777;
  --light:#eef5fa;
  --white:#fff;
  --badge:#c9d3db;
}
*{margin:0;padding:0;box-sizing:border-box}
html,body{width:1200px;height:4054px;overflow:hidden}
body{position:relative;background:var(--white);font-family:'Montserrat',sans-serif;color:var(--ink)}
.abs{position:absolute}
.btn{position:absolute;display:flex;align-items:center;justify-content:center;background:var(--navy);color:var(--white);border-radius:22px;font-size:15px;font-weight:500;letter-spacing:.3px}
.photo{position:absolute}
.brand{position:absolute;display:flex;align-items:center;gap:10px;color:var(--navy);font-weight:700}
.brand .dot{width:34px;height:34px;border-radius:50%;background:var(--navy)}

/* nav */
.hero-bg{left:0;top:0;width:1200px;height:680px;background:linear-gradient(180deg,#f4f7f9,#fbfcfd)}
.nav{left:640px;top:34px;width:350px;display:flex;justify-content:space-between;align-items:center;font-size:11px;color:#444;white-space:nowrap}
.nav .active{color:var(--navy);border:1px solid var(--navy);border-radius:50%;width:38px;height:38px;display:flex;align-items:center;justify-content:center;margin:-12px 0}
.hero-title{left:58px;top:186px;font-family:'Archivo',sans-serif;font-weight:800;font-size:44px;line-height:45px;color:var(--navy)}
.hero-title .soft{color:var(--grey)}
.hero-sub{left:61px;top:340px;font-family:Arial,sans-serif;font-size:16px;color:#111}
.hero-note{left:61px;top:373px;font-size:12px;line-height:20px;color:var(--muted)}
.slider{left:60px;top:576px;display:flex;gap:6px}
.slider span{width:10px;height:3px;background:#aaa}
.slider span:first-child{width:20px;background:var(--navy)}

/* about */
.eyebrow{left:0;width:1200px;text-align:center;font-size:13px;color:#333}
.section-title{left:0;width:1200px;text-align:center;font-size:31px;font-weight:500;color:var(--navy)}
.rule{height:3px;width:40px;background:var(--navy);left:580px}
.about-copy{left:183px;top:882px;width:340px;font-size:11.5px;line-height:21px;color:#555}
.about-copy p{margin-bottom:13px}

/* services */
.card{position:absolute;top:1365px;width:316px;height:376px;background:var(--white);box-shadow:0 2px 14px rgba(0,0,0,.1)}
.card .photo{left:6px;top:4px;width:304px;height:184px}
.card h3{position:absolute;top:210px;width:100%;text-align:center;font-size:20px;font-weight:500}
.card p{position:absolute;top:246px;left:22px;right:22px;text-align:center;font-size:11.5px;line-height:20px;color:#666}
.card a{position:absolute;top:326px;width:100%;text-align:center;font-size:13px;color:var(--navy);text-decoration:underline;font-weight:500}

/* stats */
.stats-title{left:0;width:1200px;text-align:center;color:var(--white)}
.stat{position:absolute;top:1967px;width:134px;height:134px;background:rgba(255,255,255,.09);color:var(--white);text-align:center}
.stat b{display:block;margin-top:22px;font-size:36px;font-weight:500}
.stat span{display:block;margin-top:4px;font-size:13px;line-height:18px}

/* trusted */
.trust-card{left:584px;top:2284px;width:486px;height:225px;border:1.5px solid var(--navy);border-radius:8px;background:var(--white);overflow:hidden}
.pill{left:27px;top:38px;padding:8px 20px;border-radius:16px;background:var(--navy);color:var(--white);font-size:11.5px;font-weight:600;letter-spacing:.4px}
.trust-text{left:29px;top:82px;width:215px;font-size:14.5px;line-height:23px;font-weight:500;color:#222}
.arrow{position:absolute;top:2487px;width:38px;height:38px;border-radius:50%;display:flex;align-items:center;justify-content:center}

/* badges */
.badge{position:absolute;top:2602px;width:104px;height:104px;border-radius:14px;background:#f2f5f8;border:2px solid var(--badge)}

/* reviews */
.review{position:absolute;top:3463px;width:440px}
.review .avatar{position:absolute;left:0;top:0;width:107px;height:104px;border-radius:48% 52% 44% 56%}
.review .stars{position:absolute;left:145px;top:0;font-size:12px;color:#333;display:flex;align-items:center;gap:6px}
.review .stars i{color:#f5b301;font-style:normal;font-size:17px;letter-spacing:1px}
.review p{position:absolute;left:145px;top:30px;width:280px;font-size:11.5px;line-height:20px;color:#666}
.review .who{position:absolute;left:145px;top:116px;font-size:12px;font-weight:600;color:var(--navy);letter-spacing:.5px}

/* footer */
.foot-h{position:absolute;top:3793px;font-size:14px;font-weight:500;color:var(--white);letter-spacing:.5px}
.foot-list{position:absolute;top:3830px;list-style:none;font-size:12px;color:var(--white)}
.foot-list li{height:26px}
.foot-list li::before{content:"";display:inline-block;width:4px;height:4px;border-radius:50%;background:#7fa8c6;margin-right:12px;vertical-align:middle}
.contact{position:absolute;left:611px;font-size:12px;color:var(--white);line-height:20px;display:flex;gap:14px}
.contact svg{flex:none;margin-top:2px}
</style>
</head>
<body>

<!-- hero -->
<div class="abs hero-bg"></div>
<div class="brand" style="left:60px;top:28px;font-size:24px;line-height:24px"><span class="dot"></span><span>MERIDALE<br><span style="font-size:14px;font-weight:500">STAFFING,LLC</span></span></div>
<nav class="abs nav">
  <span class="active">HOME</span><span>SERVICES</span><span>ABOUT US</span><span>OUR WORKS</span><span>CAREER</span>
</nav>
<div class="btn" style="left:1006px;top:24px;width:134px;height:34px;font-size:13px">CONTACT US</div>

<h1 class="abs hero-title">Find A Perfect<br><span class="soft">Candidate</span> For Your<br>Projects</h1>
<div class="abs hero-sub">We do Staff Augmentation and Operation Support.</div>
<div class="abs hero-note">We Work Alongside The Internal Recruiting Team To Assist<br>Clients To Meet And Exceed Financial Goals.</div>
<div class="btn" style="left:60px;top:425px;width:150px;height:41px">GET STARTED</div>
<div class="abs slider"><span></span><span></span><span></span><span></span></div>

<div class="photo" role="img" aria-label="Three smiling business professionals in front of a blue circular arrow" style="left:470px;top:95px;width:660px;height:570px;border-radius:50% 50% 0 0;background:radial-gradient(circle at 55% 45%,#1d5f8a 0 36%,#dfe6ec 37% 44%,transparent 45%),linear-gradient(180deg,#3a4f7a,#1f2d4e)"></div>
<svg class="abs" style="left:0;top:590px" width="1200" height="100" viewBox="0 0 1200 100">
  <path d="M0 100 V30 Q600 105 1200 10 V100 Z" fill="#fff"/>
  <path d="M0 30 Q600 105 1200 10" fill="none" stroke="#0b4a72" stroke-width="5"/>
</svg>

<!-- about -->
<div class="abs eyebrow" style="top:746px">What Is That?</div>
<h2 class="abs section-title" style="top:770px">MERIDALE STAFFING,LLC</h2>
<div class="abs rule" style="top:816px;width:56px;left:572px"></div>
<div class="abs about-copy">
  <p>Staff augmentation is an outsourcing strategy that allows companies to fill specific, temporary roles to achieve business objectives.</p>
  <p>This staffing method complements existing teams with specific talent, enhancing business capabilities or filling gaps left by members on extended leave.</p>
  <p>Lorem Ipsum has been the industry's standard dummy text ever since the 1500s, when an unknown printer took a galley of type and scrambled it to make a type specimen book. It has survived not only five</p>
</div>
<div class="btn" style="left:184px;top:1136px;width:150px;height:38px">LEARN MORE</div>
<div class="photo" style="left:786px;top:860px;width:80px;height:60px;border-radius:50%;background:var(--navy)"></div>
<div class="photo" role="img" aria-label="Two businesswomen shaking hands in a bright office" style="left:641px;top:880px;width:382px;height:310px;border-radius:48% 52% 40% 60% / 50% 45% 55% 50%;background:linear-gradient(120deg,#d9d4cf,#f2efec 45%,#c9713a 80%,#2b2b2b)"></div>

<!-- services -->
<h2 class="abs section-title" style="top:1280px">OUR SERVICES</h2>
<div class="abs rule" style="top:1325px"></div>
<div class="card" style="left:268px">
  <div class="photo" role="img" aria-label="Group of colleagues seated side by side" style="background:linear-gradient(180deg,#d8dadc,#9aa0a6 60%,#4a4e56)"></div>
  <h3>Staff Augmentation</h3>
  <p>Lorem Ipsum has been the industry's standard dummy text ever since the, when an unknown printer took a galley of type.</p>
  <a>Learn More</a>
</div>
<div class="card" style="left:615px">
  <div class="photo" role="img" aria-label="Team meeting around a wooden table" style="background:linear-gradient(180deg,#b5764f,#8c5a3c 55%,#5b4a3f)"></div>
  <h3>Operation Support</h3>
  <p>Lorem Ipsum has been the industry's standard dummy text ever since the, when an unknown printer took a galley of type.</p>
  <a>Learn More</a>
</div>

<!-- stats -->
<div class="photo" role="img" aria-label="Professional working on a laptop, tinted blue" style="left:0;top:1815px;width:1200px;height:381px;background:linear-gradient(90deg,#0a4a72,#245f86 50%,#0b4a72)"></div>
<svg class="abs" style="left:0;top:2088px" width="1200" height="110" viewBox="0 0 1200 110"><path d="M0 5 Q600 210 1200 5 V110 H0 Z" fill="#fff"/></svg>
<div class="abs stats-title" style="top:1878px;font-size:13px">Quick Facts</div>
<h2 class="abs stats-title" style="top:1900px;font-size:31px;font-weight:500">Our Success In Numbers</h2>
<div class="stat" style="left:309px"><b>8+</b><span>Countries<br>Served</span></div>
<div class="stat" style="left:458px"><b>28+</b><span>Awards<br>Won</span></div>
<div class="stat" style="left:608px"><b>85+</b><span>Satisfied<br>Clients</span></div>
<div class="stat" style="left:756px"><b>100+</b><span>Projects</span></div>

<!-- trusted -->
<div class="abs" style="left:132px;top:2333px;font-size:12.5px;color:#333">Our Works</div>
<h2 class="abs" style="left:132px;top:2356px;font-size:32px;line-height:36px;font-weight:500;color:var(--navy)">WE ARE A TRUSTED<br>PARTNER</h2>
<div class="abs" style="left:132px;top:2440px;width:40px;height:3px;background:var(--navy)"></div>
<div class="abs" style="left:132px;top:2455px;font-size:13px;color:#333">Recognized By The Industry</div>
<div class="abs trust-card">
  <div class="abs pill">PROJECT NAME</div>
  <div class="abs trust-text">Lorem Ipsum has Been the Industry's Standard Dummy Text Ever Since the when.</div>
  <div class="photo" role="img" aria-label="Smiling woman with glasses at a desk" style="left:242px;top:0;width:244px;height:225px;background:linear-gradient(180deg,#e6e4df,#cfc9c0 50%,#2d3f66)"></div>
</div>
<div class="arrow" style="left:649px;background:var(--navy)"><svg width="16" height="12" viewBox="0 0 16 12"><path d="M15 6H2M6 1L1 6l5 5" stroke="#fff" stroke-width="1.6" fill="none"/></svg></div>
<div class="arrow" style="left:699px;background:#fff;border:1.5px solid var(--navy)"><svg width="16" height="12" viewBox="0 0 16 12"><path d="M1 6h13M10 1l5 5-5 5" stroke="#0b4a72" stroke-width="1.6" fill="none"/></svg></div>

<!-- recognition badges -->
<div class="badge" role="img" aria-label="Industry listing badge" style="left:401px"></div>
<div class="badge" role="img" aria-label="Council membership badge" style="left:537px"></div>
<div class="badge" role="img" aria-label="Certification badge" style="left:685px"></div>

<!-- join -->
<svg class="abs" style="left:0;top:2745px" width="1200" height="425" viewBox="0 0 1200 425"><path d="M0 10 Q300 70 600 40 T1200 90 V425 H0 Z" fill="#e9f2f9"/></svg>
<div class="photo" role="img" aria-label="Smiling man with glasses holding a laptop" style="left:228px;top:2757px;width:386px;height:411px;border-radius:45% 45% 0 0;background:linear-gradient(180deg,#c7a58a,#6a2b25 45%,#4b1c19)"></div>
<h2 class="abs" style="left:733px;top:2892px;font-size:31px;font-weight:500;color:var(--navy);border-bottom:3px solid var(--navy);line-height:34px">JOIN US</h2>
<div class="abs" style="left:733px;top:2956px;width:300px;font-size:13.5px;line-height:21px;color:#222">We work Alongside the Internal Recruiting Team to Assist Clients to Meet and Exceed Financial Goals.</div>
<div class="btn" style="left:733px;top:3031px;width:167px;height:40px">VIEW POSITIONS</div>

<div class="abs" style="left:0;top:3168px;width:1200px;height:106px;background:var(--navy)"></div>
<div class="abs" style="left:0;top:3199px;width:1200px;text-align:center;font-size:34px;font-weight:500;color:var(--white)">Beat Deadlines.<span style="display:inline-block;width:1px;height:38px;background:#8fb2cc;margin-left:12px;vertical-align:middle"></span></div>

<!-- reviews -->
<h2 class="abs section-title" style="top:3354px">CLIENT REVIEWS</h2>
<div class="abs rule" style="top:3401px"></div>
<div class="review" style="left:129px">
  <div class="avatar" role="img" aria-label="Client portrait, woman with red hair" style="background:linear-gradient(160deg,#f1e9e2,#c9673a 60%,#e9dfd6)"></div>
  <div class="stars">5.0 <i>★★★★★</i></div>
  <p>Lorem Ipsum has been the industry's standard dummy text ever since the, when an unknown printer took a galley of type and scrambled it to make a type specimen book.</p>
  <div class="who">— CLIENT NAME</div>
</div>
<div class="abs" style="left:600px;top:3460px;width:1px;height:120px;background:#e2e2e2"></div>
<div class="review" style="left:633px">
  <div class="avatar" role="img" aria-label="Client portrait, man with beard and glasses" style="background:linear-gradient(160deg,#eef1f4,#b08a73 55%,#e6eaee)"></div>
  <div class="stars">5.0 <i>★★★★★</i></div>
  <p>Lorem Ipsum has been the industry's standard dummy text ever since the, when an unknown printer took a galley of type and scrambled it to make a type specimen book.</p>
  <div class="who">— CLIENT NAME</div>
</div>
<div class="abs" style="left:573px;top:3654px;display:flex;gap:5px"><span style="width:16px;height:3px;background:var(--navy)"></span><span style="width:9px;height:3px;background:#ccc"></span><span style="width:9px;height:3px;background:#ccc"></span><span style="width:9px;height:3px;background:#ccc"></span></div>

<!-- footer -->
<svg class="abs" style="left:0;top:3625px" width="1200" height="429" viewBox="0 0 1200 429"><path d="M0 0 Q600 200 1200 0 V429 H0 Z" fill="#0b4a72"/></svg>
<div class="brand" style="left:72px;top:3850px;font-size:30px;line-height:28px;color:#fff"><span class="dot" style="width:50px;height:50px;background:#fff"></span><span>MERIDALE<br><span style="font-size:17px;font-weight:500">STAFFING,LLC</span></span></div>

<div class="foot-h" style="left:337px">SITEMAP</div>
<ul class="foot-list" style="left:337px"><li>Home</li><li>Services</li><li>About Us</li><li>Our Works</li><li>Career</li></ul>

<div class="foot-h" style="left:611px">CONTACT US</div>
<div class="contact" style="top:3830px"><svg width="16" height="22" viewBox="0 0 16 22"><path d="M8 1a7 7 0 0 0-7 7c0 5 7 13 7 13s7-8 7-13a7 7 0 0 0-7-7z" fill="none" stroke="#9dbbd2" stroke-width="1.6"/><circle cx="8" cy="8" r="2.5" fill="#9dbbd2"/></svg><span>Meridale Staffing, LLC<br>101 - lorem ipsum simple text print<br>type settting industry</span></div>
<div class="contact" style="top:3900px;font-size:14px"><svg width="16" height="16" viewBox="0 0 16 16"><path d="M3 1l3 3-2 2a9 9 0 0 0 6 6l2-2 3 3-2 2C7 15 1 9 1 3z" fill="#9dbbd2"/></svg><span>555 014 2290</span></div>
<div class="contact" style="top:3932px"><svg width="18" height="14" viewBox="0 0 18 14"><rect x="1" y="1" width="16" height="12" rx="1" fill="#9dbbd2"/><path d="M1 2l8 6 8-6" stroke="#0b4a72" stroke-width="1.4" fill="none"/></svg><span>info@meridalestaffing.com</span></div>

<div class="foot-h" style="left:886px">NEWSLETTER SIGNUP !</div>
<div class="abs" style="left:886px;top:3830px;width:240px;font-size:12px;line-height:19px;color:#fff">Would you like to receive our exclusive update for signup !</div>
<div class="abs" style="left:886px;top:3875px;width:252px;height:35px;border-radius:18px;background:#fff;font-size:11.5px;color:#777;padding:11px 18px">Enter Email *</div>
<div class="btn" style="left:886px;top:3922px;width:134px;height:38px;background:transparent;border:1.5px solid #fff;font-weight:600">SUBSCRIBE</div>

<div class="abs" style="left:60px;top:4010px;width:1080px;height:1px;background:rgba(255,255,255,.25)"></div>
<div class="abs" style="left:0;top:4026px;width:1200px;text-align:center;font-size:11px;color:#fff">©2022 MERIDALE STAFFING, LLC - 2021 All rights reserved.</div>

</body>
</html>
```